Product Label with Company Logo & Product Information

I am looking for a new label design for one of my products, Candied Pecans. I am including an old label that I made, but it does not "pop" on the current packaging. See image of current packaging attached as well.

I want the design to ultimately be something that I can take and order a roll of labels/stickers. Please stick within standard label/sticker sizes (round or square). Please include final size as well.

Must Haves:
(1) Company logo (any color variation-see attached logo images).
(2) All wording on the old label
(3) Label size can not be more than 2 in. x 4 in. (I would actually like them a little smaller). They seem kind of big as they are right now.

```html
<!DOCTYPE html>
<html lang="en">
<head>
<meta charset="utf-8">
<title>Meadow Comb – Gourmet Candied Pecans Label</title>
<link rel="stylesheet" href="https://fonts.googleapis.com/css2?family=Rye&family=Ultra&family=Roboto:wght@700&display=swap">
<style>
  :root {
    --backdrop: #222222;
    --paper: #ffffff;
    --slate: #58585a;
    --slate-dark: #4a4a4c;
    --honey: #efe92a;
    --ink-light: #ffffff;
  }
  * { box-sizing: border-box; margin: 0; padding: 0; }
  html, body { width: 1200px; height: 780px; overflow: hidden; background: var(--backdrop); }
  .label {
    position: absolute; left: 40px; top: 70px;
    width: 1120px; height: 640px;
    background: var(--paper); overflow: hidden;
  }
  .label__waves { position: absolute; inset: 0; width: 100%; height: 100%; }
  .brand {
    position: absolute; left: 90px; top: 150px;
    display: flex; align-items: center; gap: 16px;
  }
  .brand__dot { width: 42px; height: 42px; border-radius: 50%; background: var(--honey); }
  .brand__name {
    font-family: "Rye", serif; font-size: 44px; color: var(--slate); line-height: 1;
  }
  .headline { position: absolute; right: 50px; top: 150px; text-align: right; white-space: nowrap; }
  .headline__top {
    font-family: "Ultra", serif; font-weight: 400; font-size: 70px; color: var(--honey);
    line-height: 1;
  }
  .headline__bottom {
    font-family: "Rye", serif; font-size: 50px; color: transparent;
    -webkit-text-stroke: 1.5px var(--honey); line-height: 1.1; margin-top: 6px;
  }
  .tagline {
    position: absolute; right: 50px; top: 330px; text-align: right; white-space: nowrap;
    font-family: "Rye", serif; font-size: 24px; line-height: 1.5; color: var(--ink-light);
  }
  .contact { position: absolute; left: 60px; top: 490px; white-space: nowrap; }
  .contact__phone {
    display: flex; align-items: center; gap: 14px;
    font-family: "Roboto", sans-serif; font-weight: 700; font-size: 34px; line-height: 1; color: var(--honey);
  }
  .contact__icon { width: 40px; height: 40px; flex: none; }
  .contact__company {
    font-family: "Rye", serif; font-size: 26px; line-height: 1.2; color: var(--ink-light); margin-top: 14px;
  }
</style>
</head>
<body>
<main class="label">
  <svg class="label__waves" viewBox="0 0 1120 640" aria-hidden="true">
    <path d="M0,380 C330,372 520,240 640,110 C730,30 900,28 1120,18 L1120,640 L0,640 Z" fill="var(--slate)"/>
    <path d="M330,375 C520,300 600,200 690,110 C780,30 900,22 980,20 C880,40 790,70 710,140 C620,230 520,330 330,375 Z" fill="var(--paper)"/>
    <path d="M0,440 C250,432 470,330 640,180 C500,345 280,462 0,468 Z" fill="var(--honey)"/>
  </svg>

  <div class="brand">
    <span class="brand__dot"></span>
    <span class="brand__name">Meadow Comb</span>
  </div>

  <div class="headline">
    <div class="headline__top">GOURMET</div>
    <div class="headline__bottom">CANDIED PECANS</div>
  </div>

  <p class="tagline">Made with Cinnamon<br>Brown Sugar &amp; Salt Order More</p>

  <div class="contact">
    <div class="contact__phone">
      <svg class="contact__icon" viewBox="0 0 44 44" aria-hidden="true">
        <polygon points="22,2 40,12 40,32 22,42 4,32 4,12" fill="var(--honey)"/>
        <path d="M14,15 q2,-3 5,-1 l2,4 q1,2 -1,3 q2,4 6,6 q1,-2 3,-1 l4,2 q2,3 -1,5 q-10,2 -18,-18 Z" fill="var(--slate)"/>
      </svg>
      <span>(555)014-2739</span>
    </div>
    <div class="contact__company">Meadow Comb Market, LLC</div>
  </div>
</main>
</body>
</html>
```